Pharmacy window design

WINDOW DIMENSIONS

4ft 8 1/2" WIDE
7ft 4 1/2" HIGH

i need a window sticker for 4 windows for the outside of a pharmacy. see attached examples. name of the pharmacy is Vista Corner

we would prefer to display products on the window signs eg. Baby care products, medicines. vitamins. fitness. veterinary, Health/ beauty etc.

Target Market(s)

Locals and Tourists

Industry/Entity Type

Pharmacy

```html
<!DOCTYPE html>
<html lang="en">
<head>
<meta charset="utf-8">
<title>Vista Corner Pharmacy – Window Banners</title>
<link rel="stylesheet" href="https://fonts.googleapis.com/css2?family=Oswald:wght@400;500;600&family=Ubuntu:wght@500;700&family=Lato:wght@900&display=swap">
<style>
  :root {
    --sheet: #444444;
    --label: #f4f4f4;
    --navy: #2f3a8e;
    --button: #3f4fae;
    --green: #7cc242;
    --green-dark: #6ab232;
    --white: #ffffff;
    --photo-light: #eef0f4;
  }
  * { box-sizing: border-box; margin: 0; padding: 0; }
  html, body { width: 1200px; height: 1200px; overflow: hidden; }
  body { background: var(--sheet); position: relative; font-family: "Oswald", sans-serif; }

  .banner { position: absolute; width: 286px; height: 501px; overflow: hidden; }
  .banner-label {
    position: absolute; width: 286px; text-align: center;
    font-family: "Ubuntu", sans-serif; font-weight: 700; font-size: 32px; color: var(--label);
  }
  .abs { position: absolute; }
  .photo { position: absolute; }

  /* brand name lockup */
  .brand { position: absolute; display: flex; align-items: center; gap: 8px; white-space: nowrap; }
  .brand-dot { border-radius: 50%; flex: none; }
  .brand-name { font-family: "Oswald", sans-serif; font-weight: 500; line-height: 1; }

  /* banner 1: product categories */
  .products { left: 205px; top: 32px; background: var(--white); }
  .category {
    position: absolute; height: 29px; border-radius: 4px;
    background: var(--button); border: 1px solid #2c3a90;
    color: var(--green); font-weight: 500; font-size: 16px; letter-spacing: -0.3px;
    display: flex; align-items: center; justify-content: center;
    white-space: nowrap; line-height: 1;
    box-shadow: 0 1px 2px rgba(0,0,0,.25);
  }
  .category-long { font-size: 14px; letter-spacing: -0.4px; }

  /* banner 2: services */
  .services { left: 695px; top: 32px; background: var(--navy); }
  .services-header { left: 0; top: 0; width: 286px; height: 81px; background: var(--white); }
  .top-bar-blue { left: 0; top: 0; width: 145px; height: 8px; background: var(--navy); }
  .top-bar-green { left: 149px; top: 0; width: 137px; height: 8px; background: var(--green); }
  .service-list { left: 12px; top: 86px; list-style: none; }
  .service-list li {
    display: flex; align-items: center; gap: 5px; height: 29.6px;
    color: var(--white); font-size: 14.5px; font-weight: 500; white-space: nowrap; letter-spacing: -0.2px;
  }
  .tick { width: 8px; height: 8px; flex: none; }
  .also-title {
    left: 126px; top: 278px; width: 152px; text-align: center; white-space: nowrap;
    color: var(--green); font-size: 20px; font-weight: 500; line-height: 26px; letter-spacing: -0.3px;
    text-decoration: underline; text-decoration-thickness: 1px; text-underline-offset: 3px;
  }
  .also-list { left: 138px; top: 306px; list-style: none; }
  .also-list li {
    display: flex; align-items: center; gap: 6px; height: 24.8px;
    color: var(--white); font-size: 16.5px; font-weight: 500; white-space: nowrap; letter-spacing: -0.2px;
  }
  .open-small { left: 118px; top: 383px; width: 138px; text-align: center; color: var(--green); font-size: 17.5px; font-weight: 500; line-height: 22px; white-space: nowrap; letter-spacing: -0.3px; }
  .hours-small { left: 102px; top: 407px; color: var(--white); font-size: 14.5px; font-weight: 500; line-height: 18px; white-space: nowrap; letter-spacing: -0.4px; }
  .insurance-band {
    left: 120px; top: 458px; width: 166px; height: 43px; background: var(--green);
    color: var(--white); font-size: 10px; font-weight: 500; letter-spacing: -0.1px;
    display: flex; align-items: center; padding-left: 4px; white-space: nowrap;
  }

  /* banner 3: opening hours */
  .hours { left: 204px; top: 606px; background: var(--navy); height: 502px; }
  .hours-header { left: 0; top: 0; width: 286px; height: 81px; background: var(--white); }
  .open-band {
    left: 0; top: 281px; width: 286px; height: 39px; background: var(--green);
    color: var(--white); font-size: 32px; font-weight: 500; letter-spacing: -0.5px; white-space: nowrap;
    display: flex; align-items: center; justify-content: center; line-height: 1;
  }
  .hours-lines {
    left: 0; top: 330px; width: 286px; text-align: center; white-space: nowrap;
    color: var(--white); font-size: 31px; font-weight: 500; line-height: 37.5px; letter-spacing: -0.5px;
  }
  .hours-footer {
    left: 0; top: 458px; width: 286px; height: 44px; background: var(--white);
    border-top: 4px solid var(--green); white-space: nowrap;
    color: var(--green); font-family: "Lato", sans-serif; font-weight: 900; font-size: 14px; letter-spacing: -0.2px;
    display: flex; align-items: center; justify-content: center;
  }

  /* banner 4: brand */
  .brand-panel { left: 696px; top: 606px; width: 287px; height: 502px; background: var(--green); }
  .brand-pattern { left: 0; top: 0; width: 287px; height: 502px; background: linear-gradient(180deg, #80c546 0%, #7ac03f 100%); }
</style>
</head>
<body>

<svg width="0" height="0" style="position:absolute" aria-hidden="true">
  <symbol id="tick" viewBox="0 0 10 10">
    <path d="M1 5.5 L4 8.5 L9 1.5" fill="none" stroke="currentColor" stroke-width="1.6" stroke-linecap="round" stroke-linejoin="round"/>
  </symbol>
</svg>

<!-- Banner 1 -->
<section class="banner products">
  <div class="brand" style="left:17px;top:16px;gap:6px">
    <span class="brand-dot" style="width:16px;height:16px;background:var(--green)"></span>
    <span class="brand-name" style="font-size:17px;color:var(--navy)">Vista Corner</span>
  </div>
  <div class="photo" role="img" aria-label="Baby care products: bottles, soap, towels and a rubber duck" style="left:150px;top:0;width:136px;height:117px;background:radial-gradient(circle at 50% 55%,#f7c6d9 0%,#f3dbe6 45%,var(--photo-light) 80%)"></div>
  <div class="category category-long" style="left:17px;top:59px;width:124px">Baby Care Products</div>

  <div class="photo" role="img" aria-label="Row of cosmetic and skincare bottles" style="left:7px;top:124px;width:138px;height:64px;background:linear-gradient(90deg,#e9dccf,#d8c0a8 40%,#efe6dc 70%,#ddd0c4)"></div>
  <div class="category" style="left:154px;top:144px;width:124px">Health/ Beauty</div>

  <div class="photo" role="img" aria-label="Veterinary medicine box" style="left:151px;top:200px;width:123px;height:72px;background:linear-gradient(160deg,#ffffff 30%,#3fb5a8 60%,#2a9c92)"></div>
  <div class="category" style="left:14px;top:228px;width:123px">Veterinary</div>

  <div class="photo" role="img" aria-label="Colourful vitamin capsules" style="left:11px;top:274px;width:130px;height:82px;border-radius:40px;background:linear-gradient(120deg,#f2a23a,#e53a2f 35%,#4caf3c 65%,#f4c23a)"></div>
  <div class="category" style="left:150px;top:297px;width:123px">Vitamins</div>

  <div class="category" style="left:21px;top:370px;width:123px">Medicines</div>
  <div class="photo" role="img" aria-label="Blister packs of tablets" style="left:159px;top:352px;width:124px;height:60px;background:linear-gradient(150deg,#f2f2f2 20%,#e55a5a 45%,#58c2a8 70%,#eeeeee)"></div>

  <div class="photo" role="img" aria-label="Tub of protein powder with a scoop" style="left:51px;top:408px;width:64px;height:80px;background:linear-gradient(90deg,#111 0%,#333 50%,#111 80%,#e8ddd0 100%)"></div>
  <div class="category" style="left:137px;top:435px;width:122px">Fitness Products</div>
</section>
<div class="banner-label" style="left:198px;top:538px">1st Banner</div>

<!-- Banner 2 -->
<section class="banner services">
  <div class="abs services-header"></div>
  <div class="abs top-bar-blue"></div>
  <div class="abs top-bar-green"></div>
  <div class="brand" style="left:40px;top:28px;gap:10px">
    <span class="brand-dot" style="width:26px;height:26px;background:var(--green)"></span>
    <span class="brand-name" style="font-size:30px;color:var(--navy)">Vista Corner</span>
  </div>

  <svg class="abs" style="left:181px;top:104px" width="105" height="168" viewBox="0 0 105 168" role="img" aria-label="Blood pressure monitor with cuff">
    <defs><linearGradient id="bp" x1="0" y1="0" x2="1" y2="1"><stop offset="0" stop-color="#e8552b"/><stop offset="1" stop-color="#ffffff"/></linearGradient></defs>
    <polygon points="42,3 105,3 105,165 42,165 10,128 10,42" fill="#f7f7f7" stroke="#ffffff" stroke-width="4"/>
    <polygon points="42,3 105,3 105,165 42,165 10,128 10,42" fill="url(#bp)" opacity=".5"/>
  </svg>

  <ul class="abs service-list">
    <li><svg class="tick" style="color:var(--green)"><use href="#tick"/></svg>Private Consultation Area</li>
    <li><svg class="tick" style="color:var(--green)"><use href="#tick"/></svg>Health advice &amp; information</li>
    <li><svg class="tick" style="color:var(--green)"><use href="#tick"/></svg>Repeat Prescriptions</li>
    <li><svg class="tick" style="color:var(--green)"><use href="#tick"/></svg>Blood Pressure Checks</li>
    <li><svg class="tick" style="color:var(--green)"><use href="#tick"/></svg>Blood Sugar Tests</li>
    <li><svg class="tick" style="color:var(--green)"><use href="#tick"/></svg>Contraception Advice</li>
  </ul>

  <svg class="abs" style="left:0;top:266px" width="121" height="132" viewBox="0 0 121 132" role="img" aria-label="Doctor, heart and checklist health icons">
    <polygon points="30,2 92,2 119,30 119,102 92,130 0,130 0,2" fill="#ffffff"/>
    <polygon points="32,8 88,8 113,33 113,99 88,124 4,124 4,8" fill="#4aa86a"/>
  </svg>

  <div class="abs also-title">ALSO AVAILABLE</div>
  <ul class="abs also-list">
    <li><svg class="tick" style="color:var(--green)"><use href="#tick"/></svg>Reading Glasses</li>
    <li><svg class="tick" style="color:var(--green)"><use href="#tick"/></svg>Medical Scrubs</li>
    <li><svg class="tick" style="color:var(--green)"><use href="#tick"/></svg>Medical Supplies</li>
  </ul>
  <div class="abs open-small">OPEN 7 DAYS A WEEK</div>
  <div class="abs hours-small">Monday-Saturday 8:30am-7pm<br>Sunday 10am-2pm</div>

  <svg class="abs" style="left:0;top:416px" width="120" height="85" viewBox="0 0 120 85" role="img" aria-label="Red first aid kit">
    <polygon points="0,0 76,0 120,44 120,85 0,85" fill="#ffffff"/>
    <polygon points="0,5 74,5 115,46 115,85 0,85" fill="#d8232a"/>
  </svg>
  <div class="abs insurance-band">WE ACCEPT ALL MAJOR INSURANCES</div>
</section>
<div class="banner-label" style="left:695px;top:538px">2nd Banner</div>

<!-- Banner 3 -->
<section class="banner hours">
  <div class="abs hours-header"></div>
  <div class="brand" style="left:36px;top:23px;gap:10px">
    <span class="brand-dot" style="width:28px;height:28px;background:var(--green)"></span>
    <span class="brand-name" style="font-size:32px;color:var(--navy)">Vista Corner</span>
  </div>
  <div class="photo" role="img" aria-label="Two green capsules with leaves inside" style="left:24px;top:100px;width:236px;height:162px;border-radius:80px;background:radial-gradient(ellipse at 50% 50%,#bfe6a2 0%,#6cc047 45%,#3c8f2a 75%,var(--navy) 100%)"></div>
  <div class="abs open-band">OPEN 7 DAYS A WEEK</div>
  <div class="abs hours-lines">Monday-Saturday<br>8:30am-7pm<br>Sunday 10am-2pm</div>
  <div class="abs hours-footer">WE ACCEPT ALL MAJOR INSURANCES</div>
</section>
<div class="banner-label" style="left:211px;top:1114px">3rd Banner</div>

<!-- Banner 4 -->
<section class="banner brand-panel">
  <div class="abs brand-pattern" role="img" aria-label="Faint pattern of medical line icons"></div>
  <div class="brand" style="left:26px;top:220px;gap:12px">
    <span class="brand-dot" style="width:34px;height:34px;background:var(--white)"></span>
    <span class="brand-name" style="font-size:38px;color:var(--white)">Vista Corner</span>
  </div>
</section>
<div class="banner-label" style="left:696px;top:1114px">4th Banner</div>

</body>
</html>
```